New Years Greeting Card Design Competition

We need a greeting card design for the new year 2014. We would like to have pictures of our daughter Meera on the card. Please find attached 5 photos of her. Please feel free to use all 5 or some of them for the design. We would like the following text on the card: "Happy New Year" and "Vik, Sunita, and Meera Deshmukhar." We would like to see designs that are very positive in style.

Target Market(s)

The greeting card is going to be sent to family and friends in different parts of the world.

Requirements
Must have
• We would like to have pictures of our daughter Meera on the card. Please find attached 5 photos of her. Please feel free to use all 5 or some of them for the design. We would like the following text on the card: "Happy New Year" and "Vik, Sunita, and Meera Deshmukhar."

```html
<!DOCTYPE html>
<html lang="en">
<head>
<meta charset="utf-8">
<title>Happy New Year 2014 – Greeting Card</title>
<link rel="stylesheet" href="https://fonts.googleapis.com/css2?family=Great+Vibes&family=Source+Sans+3:wght@400&family=Fredericka+the+Great&display=swap">
<style>
  :root {
    --card-green: #c9d27e;
    --card-green-light: #e3e6a8;
    --card-green-deep: #8fae4a;
    --pine: #3f8a2a;
    --pine-light: #7fbf3a;
    --band: rgba(205, 212, 130, 0.85);
    --ink: #1e1e1e;
    --frame: #ffffff;
    --photo-light: #eeeaf0;
    --photo-mid: #c9bfd6;
    --photo-warm: #e8d4cf;
    --digit-red: #c8453a;
    --digit-teal: #2f8f8a;
    --digit-green: #5a9a3a;
  }
  * { margin: 0; padding: 0; box-sizing: border-box; }
  html, body { width: 1200px; height: 878px; overflow: hidden; background: #f4f4f0; }
  .card {
    position: relative;
    width: 1200px; height: 878px;
    overflow: hidden;
    background: radial-gradient(ellipse at 50% 55%, var(--card-green-light) 0%, var(--card-green) 55%, var(--card-green-deep) 100%);
  }
  .garland { position: absolute; }
  .garland-top {
    left: 0; top: 0; width: 1200px; height: 150px;
    background: linear-gradient(180deg, var(--pine) 0%, var(--pine-light) 55%, rgba(201,210,126,0) 100%);
  }
  .garland-bottom {
    left: 0; bottom: 0; width: 1200px; height: 120px;
    background: linear-gradient(0deg, var(--pine) 0%, var(--pine-light) 50%, rgba(201,210,126,0) 100%);
  }
  .garland-left {
    left: 0; top: 480px; width: 130px; height: 398px;
    background: linear-gradient(90deg, var(--pine) 0%, rgba(127,191,58,0.6) 60%, rgba(201,210,126,0) 100%);
  }
  .garland-right {
    right: 0; top: 480px; width: 130px; height: 398px;
    background: linear-gradient(270deg, var(--pine) 0%, rgba(127,191,58,0.6) 60%, rgba(201,210,126,0) 100%);
  }
  .greeting-band {
    position: absolute; left: 0; top: 132px; width: 1200px; height: 328px;
    background: var(--band);
    box-shadow: 0 6px 10px rgba(60, 70, 20, 0.35);
    text-align: center;
  }
  .greeting-title {
    position: absolute; left: 0; right: 0; top: 20px;
    font-family: "Great Vibes", cursive;
    font-size: 64px; font-weight: 400; color: var(--ink);
    line-height: 1;
  }
  .greeting-year {
    position: absolute; left: 0; right: 0; top: 96px;
    font-family: "Fredericka the Great", cursive;
    font-size: 104px; line-height: 1; letter-spacing: 6px;
  }
  .greeting-year .d1 { color: var(--digit-red); }
  .greeting-year .d2 { color: var(--digit-teal); }
  .greeting-year .d3 { color: var(--digit-green); }
  .greeting-year .d4 { color: var(--digit-teal); }
  .greeting-from {
    position: absolute; left: 0; right: 0; top: 248px;
    font-family: "Great Vibes", cursive;
    font-size: 26px; color: var(--ink); line-height: 1;
  }
  .greeting-names {
    position: absolute; left: 0; right: 0; top: 280px;
    font-family: "Source Sans 3", sans-serif;
    font-size: 26px; color: var(--ink); line-height: 1;
  }
  .photo {
    position: absolute;
    border: 6px solid var(--frame);
    box-shadow: 0 3px 8px rgba(40, 50, 10, 0.4);
  }
  .photo-1 { left: 57px; top: 540px; width: 300px; height: 248px; transform: rotate(-5deg);
    background: linear-gradient(160deg, var(--photo-light) 0%, var(--photo-light) 45%, var(--photo-mid) 100%); }
  .photo-2 { left: 329px; top: 561px; width: 303px; height: 220px;
    background: linear-gradient(160deg, #4a4442 0%, #6a6260 40%, var(--photo-light) 75%, #8a8280 100%); }
  .photo-4 { left: 820px; top: 562px; width: 316px; height: 236px; transform: rotate(4deg);
    background: linear-gradient(160deg, var(--photo-warm) 0%, #f1e4e2 45%, #e9c6cc 100%); }
  .photo-3 { left: 571px; top: 518px; width: 298px; height: 214px; transform: rotate(-1deg);
    background: linear-gradient(170deg, var(--photo-light) 0%, #f2efec 45%, var(--photo-mid) 100%); }
</style>
</head>
<body>
<main class="card">
  <div class="garland garland-top" role="img" aria-label="Pine branches, holly leaves and red berries with small stars along the top edge"></div>
  <div class="garland garland-left" role="img" aria-label="Pine branches and holly with red berries at the lower left"></div>
  <div class="garland garland-right" role="img" aria-label="Pine branches and holly with red berries at the lower right"></div>
  <div class="garland garland-bottom" role="img" aria-label="Pine branches, holly leaves and small stars along the bottom edge"></div>

  <section class="greeting-band">
    <h1 class="greeting-title">Happy New Year</h1>
    <p class="greeting-year" aria-label="2014"><span class="d1">2</span><span class="d2">0</span><span class="d3">1</span><span class="d4">4</span></p>
    <p class="greeting-from">from</p>
    <p class="greeting-names">Vik, Sunita, and Meera Deshmukhar</p>
  </section>

  <div class="photo photo-1" role="img" aria-label="Photo of baby Meera wrapped in a lavender blanket"></div>
  <div class="photo photo-2" role="img" aria-label="Photo of baby Meera sleeping in a car seat wearing a knit cap"></div>
  <div class="photo photo-4" role="img" aria-label="Photo of baby Meera in a pink fleece outfit"></div>
  <div class="photo photo-3" role="img" aria-label="Photo of baby Meera awake in a lavender blanket"></div>
</main>
</body>
</html>
```